Liron Vasek Website

Website for my son who is in 7th grade in the US. This will prepare him to show people his accomplishments when applying for a job or going to college. It should have:
* A picture (or multiple pictures)
* A resume page
* A place to share your accomplishments
* Links to his other social profiles
* A contact form

Great to include:
* Internships (show some photos of it along with what you’ve learned).
* Volunteer work.
* A side hustle that you want to highlight

Website sample I like:
https://belinamorud.sitefolio-demo.com/belinamorudtavik

Target Market(s)

For jobs and colleges admissions.

Number of Pages Required

5+ page

Colors

Designer to choose colors to be used in the design.

Requirements
Must have
• * A picture (or multiple pictures)
• * A resume page
• * A place to share your accomplishments
• * Links to his other social profiles
• * A contact form
Nice to have
• Great to include:
• * Internships (show some photos of it along with what you’ve learned).
• * Volunteer work.
• * A side hustle that you want to highlight

```html
<!DOCTYPE html>
<html lang="en">
<head>
<meta charset="utf-8">
<title>Liron Vasek</title>
<link href="https://fonts.googleapis.com/css2?family=Montserrat:wght@400;600;700;800&family=Open+Sans:wght@400;600&display=swap" rel="stylesheet">
<style>
:root{
  --ink:#151515;
  --text:#3a3a3a;
  --muted:#555;
  --accent:#03a9f4;
  --accent-deep:#0a8fd8;
  --yellow:#ffc600;
  --soft:#f5f3f4;
  --white:#ffffff;
  --footer:#3a3a3a;
  --rule:#8a8a8a;
}
*{margin:0;padding:0;box-sizing:border-box}
html,body{width:1200px;height:3680px;overflow:hidden}
body{font-family:"Open Sans",Arial,sans-serif;color:var(--text);background:var(--white);position:relative}
section,header,footer{position:absolute;left:0;width:1200px}
.abs{position:absolute}
.heading{font-family:"Montserrat",Arial,sans-serif;font-weight:800;color:var(--ink);text-align:center;left:0;width:1200px;letter-spacing:.5px}
.rule{position:absolute;width:76px;height:8px}
.rule::before,.rule::after{content:"";position:absolute;height:1px;background:var(--rule)}
.rule::before{left:0;top:0;width:60px}
.rule::after{left:16px;top:6px;width:60px}
.rule.light::before,.rule.light::after{background:#e6f6ff}

/* hero */
.hero{top:0;height:550px;background:linear-gradient(180deg,#6f8fae 0%,#a7b3c2 22%,#f2a57a 36%,#c9866a 44%,#4b5563 60%,#2d333d 100%)}
.brand{left:129px;top:27px;font-family:"Montserrat",sans-serif;font-weight:800;font-size:28px;color:var(--white);letter-spacing:.5px}
.nav{right:0;top:27px;width:1200px;height:20px}
.nav a{position:absolute;font-family:"Montserrat",sans-serif;font-weight:700;font-size:13.5px;color:var(--white);text-decoration:none;letter-spacing:.3px}
.dots{left:549px;top:489px;display:flex;gap:13px}
.dots span{width:10px;height:10px;border-radius:50%;background:var(--white)}
.dots span.active{background:#e4182b;box-shadow:0 0 0 2px var(--white)}

/* about */
.about{top:550px;height:610px;background:var(--soft)}
.about .heading{top:48px;font-size:34px}
.about p{position:absolute;left:330px;width:540px;top:142px;font-size:15.5px;line-height:23.3px;text-align:center;color:var(--muted)}
.photo{position:absolute}

/* accomplishments */
.accomplish{top:1160px;height:533px;background:var(--white)}
.accomplish .heading{top:52px;font-size:31px}
.divider{left:600px;top:176px;width:1px;height:300px;background:#ddd}
.item{position:absolute;width:390px;font-size:15.5px;line-height:23.3px;color:var(--text)}
.item svg{position:absolute;left:-29px;top:5px}

/* internships */
.internships{top:1693px;height:686px;background:linear-gradient(120deg,#eeeeef 0%,#f7f7f8 30%,#ececed 55%,#f8f8f9 80%,#ededee 100%)}
.internships .heading{top:49px;font-size:31px}
.grid{left:131px;top:157px;width:920px;height:474px;display:grid;grid-template-columns:repeat(4,230px);grid-template-rows:237px 237px;box-shadow:0 2px 6px rgba(0,0,0,.06)}
.card{background:var(--white);padding:32px 30px 0 30px}
.card h3{font-family:"Montserrat",sans-serif;font-weight:700;font-size:17px;color:var(--ink);margin-bottom:8px}
.card p{font-size:12.6px;line-height:17.6px;color:var(--muted);width:175px;padding-left:3px}
.card a{display:inline-block;margin-top:14px;margin-left:3px;font-family:"Montserrat",sans-serif;font-weight:700;font-size:12.5px;color:var(--accent);text-decoration:underline}
.shot{width:230px;height:237px}

/* volunteer */
.volunteer{top:2379px;height:464px;background:radial-gradient(ellipse at 70% 40%,#e9f3fa 0%,#c6dfef 45%,#a8cde6 100%)}
.volunteer h2{left:130px;top:64px;font-family:"Montserrat",sans-serif;font-weight:800;font-size:40px;color:var(--ink);position:absolute}
.volunteer p{left:130px;top:169px;width:575px;font-size:16.5px;line-height:24.7px;color:var(--text);position:absolute}
.btn{position:absolute;left:133px;top:348px;width:161px;height:50px;background:var(--accent);color:var(--white);font-family:"Montserrat",sans-serif;font-weight:700;font-size:15.5px;display:flex;align-items:center;justify-content:center;text-decoration:none}
.globe{left:829px;top:114px;width:271px;height:350px;background:radial-gradient(circle at 50% 32%,#5b86b8 0%,#7a9fc3 30%,#d9b39b 55%,rgba(217,179,155,.4) 80%,transparent 100%)}

/* contact */
.contact{top:2843px;height:600px;background:linear-gradient(180deg,#05aff0 0%,#0aa6ea 60%,#209fe0 100%)}
.contact .heading{top:62px;font-size:30px;color:var(--white)}
.field{position:absolute;left:351px;width:498px;background:var(--white);font-size:12.5px;color:#444;padding:14px 18px;letter-spacing:.3px}
.submit{position:absolute;left:351px;top:480px;width:498px;height:56px;background:var(--yellow);color:#3b3b3b;font-family:"Montserrat",sans-serif;font-weight:800;font-size:25px;display:flex;align-items:center;justify-content:center;box-shadow:0 2px 0 rgba(0,0,0,.15)}

/* footer */
.footer{top:3443px;height:237px;background:var(--footer);color:var(--white);text-align:center}
.footer .name{position:absolute;left:0;width:1200px;top:50px;font-family:"Montserrat",sans-serif;font-weight:800;font-size:41px}
.footer nav{position:absolute;left:0;width:1200px;top:118px;font-size:13px;color:#ddd;letter-spacing:.3px}
.footer nav span{margin:0 10px;color:#ccc}
.footer small{position:absolute;left:0;width:1200px;top:171px;font-size:11px;color:#eee}
</style>
</head>
<body>

<header class="hero" role="img" aria-label="Photo of a city skyline at sunset">
  <div class="abs brand">LIRON VASEK</div>
  <nav class="abs nav">
    <a style="left:509px">HOME</a>
    <a style="left:583px">RESUME</a>
    <a style="left:673px">PORTFOLIO</a>
    <a style="left:786px">ACHIEVEMENTS</a>
    <a style="left:933px">BLOG</a>
    <a style="left:1002px">CONTACT</a>
  </nav>
  <div class="abs dots"><span></span><span></span><span class="active"></span><span></span><span></span></div>
</header>

<section class="about">
  <h2 class="abs heading">ABOUT ME</h2>
  <div class="rule" style="left:564px;top:100px"></div>
  <p>Lorem ipsum dolor sit amet, consectetur adipiscing elit sed do eiusmod tempor incididunt ut labore et dolore magna aliqua&nbsp; Ut enim ad minim veniam uis nostrud exercitation ullamco laboris nisi ut aliquip ex ea commodo consequat. Duis aute irure dolor in reprehenderit in voluptate velit esse cillum.</p>
  <div class="photo" style="left:160px;top:296px;width:287px;height:258px;background:linear-gradient(180deg,#e9b35a 0%,#b98a64 35%,#7d3f33 65%,#5c3a2e 100%)" role="img" aria-label="Photo of a brick school building"></div>
  <div class="photo" style="left:456px;top:296px;width:287px;height:258px;background:linear-gradient(135deg,#7a5a3e 0%,#a98764 40%,#d9cfc4 75%,#eeeae4 100%)" role="img" aria-label="Photo of a boy working on a laptop"></div>
  <div class="photo" style="left:750px;top:296px;width:287px;height:258px;background:linear-gradient(180deg,#6e7590 0%,#c9876d 28%,#6b4a45 55%,#3d2e2e 100%)" role="img" aria-label="Photo of a city seen from above"></div>
</section>

<section class="accomplish">
  <h2 class="abs heading">ACCOMPLISHMENTS</h2>
  <div class="rule" style="left:564px;top:104px"></div>
  <div class="abs divider"></div>

  <div class="item" style="left:187px;top:172px"><svg width="14" height="12" viewBox="0 0 14 12"><path d="M1 6l4 4 8-9" fill="none" stroke="#03a9f4" stroke-width="2.6"/></svg>Lorem ipsum dolor sit amet onsectetur adi elit sed do eiusmod tempor incididunt</div>
  <div class="item" style="left:187px;top:253px"><svg width="14" height="12" viewBox="0 0 14 12"><path d="M1 6l4 4 8-9" fill="none" stroke="#03a9f4" stroke-width="2.6"/></svg>But I must explain to you how all this mistaken idea of denouncing pleasure.</div>
  <div class="item" style="left:187px;top:335px"><svg width="14" height="12" viewBox="0 0 14 12"><path d="M1 6l4 4 8-9" fill="none" stroke="#03a9f4" stroke-width="2.6"/></svg>On the other hand, we denounce with righteous indignation and dislike men.</div>
  <div class="item" style="left:187px;top:418px"><svg width="14" height="12" viewBox="0 0 14 12"><path d="M1 6l4 4 8-9" fill="none" stroke="#03a9f4" stroke-width="2.6"/></svg>Occur that pleasures have to be repudiated and annoyances accepted he wise man.</div>

  <div class="item" style="left:684px;top:172px"><svg width="14" height="12" viewBox="0 0 14 12"><path d="M1 6l4 4 8-9" fill="none" stroke="#03a9f4" stroke-width="2.6"/></svg>Sed ut perspiciatis unde omnis iste natus error sit voluptatem accusantium doloremque.</div>
  <div class="item" style="left:684px;top:253px"><svg width="14" height="12" viewBox="0 0 14 12"><path d="M1 6l4 4 8-9" fill="none" stroke="#03a9f4" stroke-width="2.6"/></svg>At vero eos et accusamus et iusto odio dignissimos ducimus qui blanditiis.</div>
  <div class="item" style="left:684px;top:335px"><svg width="14" height="12" viewBox="0 0 14 12"><path d="M1 6l4 4 8-9" fill="none" stroke="#03a9f4" stroke-width="2.6"/></svg>when our power of choice is untrammelled and when nothing prevents our being able to do</div>
  <div class="item" style="left:684px;top:418px"><svg width="14" height="12" viewBox="0 0 14 12"><path d="M1 6l4 4 8-9" fill="none" stroke="#03a9f4" stroke-width="2.6"/></svg>He rejects pleasures to secure other greater pleasures, or else he endures pains.</div>
</section>

<section class="internships">
  <h2 class="abs heading">INTERNSHIPS</h2>
  <div class="rule" style="left:564px;top:100px"></div>
  <div class="abs grid">
    <div class="shot" style="background:linear-gradient(135deg,#5e5a55 0%,#9c8a7a 45%,#d8d2cc 100%)" role="img" aria-label="Photo of a teacher helping students at computers"></div>
    <div class="card"><h3>LOREM IPSUM</h3><p>Lorem ipsum dolor sit amet consectetur adipiscing elit sed do eiusmod tempor incididunt&nbsp; ut&nbsp; he rejects pleasures to secure other greater pleasures.</p><a>READ MORE</a></div>
    <div class="shot" style="background:linear-gradient(135deg,#b7b3ad 0%,#8d7462 45%,#e2ded9 100%)" role="img" aria-label="Photo of students building a small robot"></div>
    <div class="card"><h3>LOREM IPSUM</h3><p>Lorem ipsum dolor sit amet consectetur adipiscing elit sed do eiusmod tempor incididunt&nbsp; ut&nbsp; he rejects pleasures to secure other greater pleasures.</p><a>READ MORE</a></div>

    <div class="card"><h3>LOREM IPSUM</h3><p>Lorem ipsum dolor sit amet consectetur adipiscing elit sed do eiusmod tempor incididunt ut&nbsp; he rejects pleasures to secure other greater pleasures.</p><a>READ MORE</a></div>
    <div class="shot" style="background:linear-gradient(135deg,#3f4650 0%,#8a7566 45%,#d5d5d8 100%)" role="img" aria-label="Photo of a teacher and children around a laptop"></div>
    <div class="card"><h3>LOREM IPSUM</h3><p>Lorem ipsum dolor sit amet consectetur adipiscing elit sed do eiusmod tempor incididunt ut&nbsp; he rejects pleasures to secure other greater pleasures.</p><a>READ MORE</a></div>
    <div class="shot" style="background:linear-gradient(135deg,#8f8d88 0%,#7a5b48 45%,#e8e6e3 100%)" role="img" aria-label="Photo of a father and children using a laptop"></div>
  </div>
</section>

<section class="volunteer">
  <h2>VOLUNTEER</h2>
  <div class="rule" style="left:137px;top:120px"></div>
  <p>On the other hand, we denounce with righteous indignation and dislike men who are so beguiled and demoralized by the charms of pleasure of the moment, so blinded by desire, that they cannot foresee the pain and trouble that are bound to ensue; and equal blame belongs to those who fail in their duty through weakness of will, which is the same as saying through shrinking from toil and pain.</p>
  <a class="btn">READ MORE</a>
  <div class="abs globe" role="img" aria-label="Photo of hands holding up a globe"></div>
</section>

<section class="contact">
  <h2 class="abs heading">CONTACT ME</h2>
  <div class="rule light" style="left:564px;top:102px"></div>
  <div class="field" style="top:157px;height:43px">NAME</div>
  <div class="field" style="top:211px;height:46px">E MAIL</div>
  <div class="field" style="top:266px;height:45px">PHONE</div>
  <div class="field" style="top:320px;height:146px">MESSAGE</div>
  <div class="submit">SUBMIT</div>
</section>

<footer class="footer">
  <div class="name">LIRON VASEK</div>
  <nav>HOME<span>\</span>PORTFOLIO<span>\</span>RESUME<span>\</span>ACHIEVEMENTS<span>\</span>BLOG<span>\</span>CONTACT</nav>
  <small>Copyrights @ 2019 All Rights Reserved</small>
</footer>

</body>
</html>
```